Business cards to launch an education platform

Hi,
I am looking at having new business cards designed.
I am a startup, developing a web platform for schools and university, the education world. It's an online assessment system.
I would like a card that looks classy, and that is using the colors and the font of my logo.

I have attached:
1) my logo
2) A business card that I have designed quickly so you can have all the information required in the card, but I really don't like it.
3) The font that I am using (Lato Regular) to design my web platform
4) Some screenshots of my web platform so you can have a look at the style that I have.

Target Market(s)

Major market: Education system: Schools and university
Minor markets: Business in general

Industry/Entity Type

Business

Contact Information for Business Card

Clara Fenwick
Director

M: 0437 518 902
E: clara.fenwick@amberLoomSystems.com.au

Requirements
Must have
• The colors of my logo

```html
<!DOCTYPE html>
<html lang="en">
<head>
<meta charset="utf-8">
<title>Amber Loom Systems – Business Cards</title>
<link rel="stylesheet" href="https://fonts.googleapis.com/css2?family=Lato:wght@400;700&display=swap">
<style>
  :root {
    --page-bg: #3b3633;
    --card-bg: #161618;
    --card-edge: #0c0c0d;
    --brand-blue: #1c8fd8;
    --accent-cyan: #18c0f2;
    --text-white: #f2f2f2;
    --rule-white: #e8e8e8;
  }
  * { box-sizing: border-box; margin: 0; padding: 0; }
  html, body {
    width: 1200px;
    height: 780px;
    overflow: hidden;
    background: var(--page-bg);
    font-family: "Lato", sans-serif;
  }
  .canvas {
    position: relative;
    width: 1200px;
    height: 780px;
    display: flex;
    align-items: center;
    justify-content: center;
    gap: 50px;
  }
  .card {
    position: relative;
    width: 540px;
    height: 310px;
    background: var(--card-bg);
    border-radius: 6px;
    box-shadow: 0 10px 24px rgba(0,0,0,0.45);
    color: var(--text-white);
  }
  .brand {
    display: flex;
    align-items: center;
    gap: 12px;
  }
  .brand-square {
    width: 34px;
    height: 34px;
    background: var(--brand-blue);
    flex: none;
  }
  .brand-name {
    font-family: "Lato", sans-serif;
    font-weight: 400;
    color: var(--brand-blue);
    letter-spacing: 2px;
    line-height: 1.05;
    text-transform: uppercase;
  }
  /* Front */
  .card-front .brand {
    position: absolute;
    top: 38px;
    left: 150px;
  }
  .card-front .brand-name { font-size: 20px; }
  .card-front .divider {
    position: absolute;
    top: 128px;
    left: 30px;
    width: 290px;
    height: 1px;
    background: var(--rule-white);
  }
  .person {
    position: absolute;
    top: 142px;
    right: 34px;
    text-align: right;
  }
  .person-name {
    font-size: 30px;
    font-weight: 400;
    color: var(--accent-cyan);
    line-height: 1.1;
  }
  .person-role {
    font-size: 17px;
    color: var(--text-white);
    margin-top: 4px;
  }
  .contact-list {
    position: absolute;
    left: 30px;
    bottom: 36px;
    list-style: none;
    font-size: 13px;
    line-height: 1;
  }
  .contact-item {
    display: flex;
    align-items: center;
    gap: 8px;
    margin-top: 8px;
  }
  .contact-icon {
    width: 13px;
    height: 13px;
    flex: none;
  }
  /* Back */
  .card-back {
    display: flex;
    align-items: center;
    justify-content: center;
  }
  .card-back .brand-square { width: 46px; height: 46px; }
  .card-back .brand-name { font-size: 28px; }
</style>
</head>
<body>
<main class="canvas">
  <section class="card card-front" aria-label="Business card front">
    <div class="brand">
      <span class="brand-square"></span>
      <span class="brand-name">Amber Loom<br>Systems</span>
    </div>
    <div class="divider"></div>
    <div class="person">
      <p class="person-name">Clara Fenwick</p>
      <p class="person-role">Director</p>
    </div>
    <ul class="contact-list">
      <li class="contact-item">
        <svg class="contact-icon" viewBox="0 0 14 14" aria-hidden="true">
          <rect width="14" height="14" rx="2" fill="var(--accent-cyan)"/>
          <path d="M4.2 3.2c.4-.3.8-.2 1 .2l.7 1.3c.2.4.1.7-.2 1l-.5.4c.4.9 1.1 1.6 2 2l.4-.5c.3-.3.6-.4 1-.2l1.3.7c.4.2.5.6.2 1l-.6.8c-.3.4-.9.5-1.4.3C6 9.5 4.5 8 3.8 6.1c-.2-.5-.1-1.1.3-1.4z" fill="var(--card-bg)"/>
        </svg>
        <span>0437 518 902</span>
      </li>
      <li class="contact-item">
        <svg class="contact-icon" viewBox="0 0 14 14" aria-hidden="true">
          <rect width="14" height="14" rx="2" fill="var(--accent-cyan)"/>
          <rect x="3" y="4.5" width="8" height="5.5" fill="none" stroke="var(--card-bg)" stroke-width="1"/>
          <path d="M3 4.8 7 7.6 11 4.8" fill="none" stroke="var(--card-bg)" stroke-width="1"/>
        </svg>
        <span>clara.fenwick@amberLoomSystems.com.au</span>
      </li>
    </ul>
  </section>

  <section class="card card-back" aria-label="Business card back">
    <div class="brand">
      <span class="brand-square"></span>
      <span class="brand-name">Amber Loom<br>Systems</span>
    </div>
  </section>
</main>
</body>
</html>
```